Veltmoor Capital Stationary Design

We have selected a logo as our winner, we now need a full stationary set to be in the same theme.
Required:
- Letter Head
- Business Card Template
- Custom Envelopes
- A5 Notepad Design (Front cover and content pages. Content pages blank(no lines) but with our branding on them,)
- With Compliments Slip
Updates

Hey All,

We have changed the colour scheme of our logo. Our apologies if anyone has begun designing based off the old scheme. Please see the updated scheme in the brief,

Oliver

Target Market(s)

Target market is experienced property developers and financial institutions.

Industry/Entity Type

Commercial Finance

Font styles to use
Serif

Colors
0054AA
0677BA
7BADD7
CADEEF
E8F1F8
0094D4
00A9DD
6FCCEA
C7EBF8
E9F6FB
00AB8E
00BBA5
67D7C9
C6EFE9
E9F9F6
59FF00
82FF00
B8FF75
E3FFCB
F4FFEA

```html
<!DOCTYPE html>
<html lang="en">
<head>
<meta charset="utf-8">
<title>Veltmoor Capital – Business Card</title>
<link rel="stylesheet" href="https://fonts.googleapis.com/css2?family=Lora:wght@400;500;700&display=swap">
<style>
  :root {
    --backdrop: #6d6d6d;
    --card-white: #ffffff;
    --brand-blue: #0054AA;
    --brand-teal: #00AB8E;
    --ink: #2b2b2b;
  }
  * { margin: 0; padding: 0; box-sizing: border-box; }
  html, body {
    width: 1200px; height: 801px; overflow: hidden;
    background: var(--backdrop);
    font-family: "Lora", serif;
  }
  .card-set {
    position: absolute; inset: 0;
    display: flex; align-items: center; justify-content: center; gap: 40px;
  }
  .card {
    position: relative;
    width: 540px; height: 309px;
    border-radius: 16px;
    overflow: hidden;
  }
  .card--front { background: var(--card-white); }
  .card--back { background: var(--brand-blue); display: flex; align-items: center; justify-content: center; }

  .front-swoosh { position: absolute; inset: 0; width: 100%; height: 100%; }

  .brand-name {
    display: flex; align-items: center;
    font-weight: 700; line-height: 1; white-space: nowrap;
  }
  .brand-square { flex: none; }
  .card--front .brand-name {
    position: absolute; left: 36px; top: 124px;
    font-size: 22px; color: var(--brand-blue); gap: 8px;
  }
  .card--front .brand-square { width: 12px; height: 12px; background: var(--brand-blue); }

  .card--back .brand-name { font-size: 44px; color: #ffffff; gap: 14px; }
  .card--back .brand-square { width: 22px; height: 22px; background: #ffffff; }

  .divider {
    position: absolute; left: 262px; top: 62px;
    width: 1.5px; height: 160px;
    background: var(--brand-teal);
  }

  .contact-block {
    position: absolute; left: 282px; top: 52px;
    color: var(--ink);
  }
  .person-name {
    font-size: 19px; font-weight: 700; color: var(--brand-teal);
    letter-spacing: 0.5px; text-transform: uppercase;
  }
  .person-title { font-size: 12.5px; margin-top: 3px; }
  .contact-list { list-style: none; margin-top: 16px; font-size: 11.5px; }
  .contact-list li { display: flex; align-items: center; gap: 6px; line-height: 1.55; }
  .contact-list svg { width: 10px; height: 10px; fill: var(--brand-teal); flex: none; }
  .address { font-size: 11.5px; font-style: normal; margin-top: 14px; line-height: 1.55; }
</style>
</head>
<body>
<main class="card-set">
  <section class="card card--front" aria-label="Business card front">
    <svg class="front-swoosh" viewBox="0 0 540 309" preserveAspectRatio="none" aria-hidden="true">
      <path d="M58 309 C250 300 430 245 540 182 L540 309 Z" fill="var(--brand-teal)"/>
      <path d="M34 309 C235 293 418 230 540 160" fill="none" stroke="var(--brand-blue)" stroke-width="5"/>
    </svg>

    <div class="brand-name">
      <span class="brand-square"></span>
      <span class="brand-text">Veltmoor Capital</span>
    </div>

    <div class="divider"></div>

    <div class="contact-block">
      <h1 class="person-name">Oliver Hartwell</h1>
      <p class="person-title">Managing Director</p>
      <ul class="contact-list">
        <li><svg viewBox="0 0 10 10"><path d="M2 0.5 L3.8 0.5 L4.4 3 L3.2 3.9 C3.8 5.2 4.8 6.2 6.1 6.8 L7 5.6 L9.5 6.2 L9.5 8 C9.5 8.9 8.9 9.5 8 9.5 C4 9.3 0.7 6 0.5 2 C0.5 1.1 1.1 0.5 2 0.5 Z"/></svg>555 018 247</li>
        <li><svg viewBox="0 0 10 10"><path d="M0.5 2 L9.5 2 L9.5 8.5 L0.5 8.5 Z M0.5 2 L5 5.5 L9.5 2" stroke="#fff" stroke-width="0.8"/></svg>hello@veltmoorcap.com</li>
        <li><svg viewBox="0 0 10 10"><circle cx="5" cy="5" r="4.5"/><path d="M0.5 5 H9.5 M5 0.5 C3 3 3 7 5 9.5 M5 0.5 C7 3 7 7 5 9.5" stroke="#fff" stroke-width="0.7" fill="none"/></svg>www.veltmoorcap.com</li>
      </ul>
      <address class="address">1180 Larkspur Quay<br>Seabrook CA 90417</address>
    </div>
  </section>

  <section class="card card--back" aria-label="Business card back">
    <div class="brand-name">
      <span class="brand-square"></span>
      <span class="brand-text">Veltmoor Capital</span>
    </div>
  </section>
</main>
</body>
</html>
```